Panty packaging

what we are looking for is 1 of a kind packaging for women's panties. It should have the same theme for all styles but a different outline or a color code setting the difference between styles. Most company's are packaging in a poly bag or hanger, what we are looking for is a box packaging. also customer should be able to see whats in the box without having to open the box. If there are different colors, the window should show that. We want to be able to customize the design for different styles and for 1 color package or multi color package. It should be sleek and sophisticated. Box does not have to be square, it can have curved edges or be totally round, the most important thins is that it should be stack-able. Sometimes the box will hold a pack of 3 and sometimes a single item, so box height may vary. We need a graphic on the box to indicate the style, for example: hipster, brief, hi cut, or lo cut. box needs a space to put a small size chart. Out logo can be color changed to match theme and background colors, just stick with the 3 colors, black, white, and magneta.
Female market all ages. upscale market
It Company

```html
<!DOCTYPE html>
<html lang="en">
<head>
<meta charset="utf-8">
<title>Velvane Elegant Panties – Round Box Wraps</title>
<link rel="stylesheet" href="https://fonts.googleapis.com/css2?family=Montserrat:wght@400;600&family=Open+Sans:wght@400;600;700&display=swap">
<style>
  :root {
    --black: #1c1c1c;
    --charcoal: #2b2b2b;
    --grey: #a9a9a9;
    --grey-light: #d2d2d2;
    --white: #ffffff;
    --magenta: #e2127f;
    --magenta-deep: #8a0c4f;
    --beige: #cdbfa6;
    --beige-light: #e6dccb;
    --stage: #e9e9e9;
  }
  * { box-sizing: border-box; margin: 0; padding: 0; }
  html, body { width: 1200px; height: 1000px; overflow: hidden; }
  body {
    background: var(--stage);
    font-family: "Open Sans", Arial, sans-serif;
  }
  .range {
    width: 1200px; height: 1000px;
    display: grid;
    grid-template-columns: repeat(3, 260px);
    grid-template-rows: repeat(3, 260px);
    column-gap: 20px; row-gap: 40px;
    padding: 70px 190px;
  }
  .wrap {
    position: relative;
    background: var(--pattern);
    border-radius: 4px;
    box-shadow: 0 2px 6px rgba(0,0,0,.18);
    overflow: hidden;
  }
  .wrap__lid-line {
    position: absolute; left: 0; right: 0; top: 52px;
    height: 3px; background: var(--white); opacity: .9;
  }
  .label {
    position: absolute; left: 50%; top: 92px;
    transform: translateX(-50%);
    width: 138px; height: 132px;
    border-radius: 40px;
    background: var(--frame);
    border: 4px solid var(--frame-edge);
    display: flex; align-items: center; justify-content: center;
  }
  .label__plate {
    width: 106px; height: 100px;
    border-radius: 50%;
    background: var(--plate);
    display: flex; flex-direction: column; align-items: center; justify-content: center;
  }
  .brand {
    font-family: "Montserrat", Arial, sans-serif;
    font-weight: 400; font-size: 17px; letter-spacing: .5px;
    color: #4a4a4a; line-height: 1;
  }
  .tagline {
    font-size: 7px; font-weight: 600; color: #555;
    margin-top: 3px;
  }
  .style-tag {
    margin-top: 8px;
    padding: 2px 10px;
    border-radius: 50%;
    background: var(--pill);
    color: var(--pill-text);
    font-size: 10px; font-weight: 700;
    box-shadow: inset 0 0 0 1px rgba(0,0,0,.15);
  }
  .bow {
    position: absolute; left: 50%; top: 72px;
    transform: translateX(-50%);
    width: 46px; height: 26px;
    border-radius: 6px;
    background: var(--black);
  }
  .size-badge {
    position: absolute; right: 30px; top: 90px;
    width: 28px; height: 28px; border-radius: 50%;
    background: var(--beige);
    border: 1px solid #8c7f6a;
    font-size: 8px; font-weight: 700; color: #3a3a3a;
    display: flex; align-items: center; justify-content: center;
  }

  .wrap--charcoal-dots  { --pattern: var(--charcoal); }
  .wrap--magenta-stripes { --pattern: var(--magenta-deep); }
  .wrap--white-magenta-dots { --pattern: #f6c9df; }
  .wrap--black-magenta-dots { --pattern: #6b0c3c; }
  .wrap--white-grey-dots { --pattern: #e4e4e4; }
  .wrap--black-stripes { --pattern: #3a3a3a; }
  .wrap--beige-stripes { --pattern: #d9ccb4; }
  .wrap--white-stripes { --pattern: #efefef; }

  .label--pink-stripes { --frame: #f3c6dc; --frame-edge: var(--magenta); --plate: var(--white); --pill: var(--grey-light); --pill-text: #333; }
  .label--grey-dots { --frame: var(--grey-light); --frame-edge: #e0e0e0; --plate: var(--white); --pill: var(--beige); --pill-text: var(--magenta); }
  .label--magenta-grey { --frame: #b8b8b8; --frame-edge: var(--magenta); --plate: #bdbdbd; --pill: #8f8f8f; --pill-text: var(--white); }
  .label--beige-stripes { --frame: var(--beige-light); --frame-edge: var(--black); --plate: var(--beige); --pill: var(--beige); --pill-text: #333; }
  .label--magenta-beige { --frame: var(--beige); --frame-edge: var(--magenta); --plate: var(--beige); --pill: #b8a888; --pill-text: var(--white); }
  .label--magenta-white { --frame: var(--white); --frame-edge: var(--magenta); --plate: var(--white); --pill: var(--beige); --pill-text: #333; }
</style>
</head>
<body>
<main class="range">

  <article class="wrap wrap--charcoal-dots" role="img" aria-label="Black wrap with grey polka dots">
    <div class="wrap__lid-line"></div>
    <div class="label label--pink-stripes"><div class="label__plate"><span class="brand">Velvane</span><span class="tagline">Elegant Panties</span><span class="style-tag">lo cut</span></div></div>
    <div class="bow" role="img" aria-label="Black satin bow"></div>
    <div class="size-badge">size</div>
  </article>

  <article class="wrap wrap--magenta-stripes" role="img" aria-label="Black and magenta vertical stripes">
    <div class="wrap__lid-line"></div>
    <div class="label label--grey-dots"><div class="label__plate"><span class="brand">Velvane</span><span class="tagline">Elegant Panties</span><span class="style-tag">hipster</span></div></div>
    <div class="bow" role="img" aria-label="Black satin bow"></div>
    <div class="size-badge">size</div>
  </article>

  <article class="wrap wrap--white-magenta-dots" role="img" aria-label="White wrap with magenta polka dots">
    <div class="wrap__lid-line"></div>
    <div class="label label--grey-dots"><div class="label__plate"><span class="brand">Velvane</span><span class="tagline">Elegant Panties</span><span class="style-tag">hipster</span></div></div>
    <div class="bow" role="img" aria-label="Black satin bow"></div>
    <div class="size-badge">size</div>
  </article>

  <article class="wrap wrap--black-magenta-dots" role="img" aria-label="Black wrap with magenta polka dots">
    <div class="wrap__lid-line"></div>
    <div class="label label--magenta-grey"><div class="label__plate"><span class="brand">Velvane</span><span class="tagline">Elegant Panties</span><span class="style-tag">lo cut</span></div></div>
    <div class="bow" role="img" aria-label="Black satin bow"></div>
    <div class="size-badge">size</div>
  </article>

  <article class="wrap wrap--white-grey-dots" role="img" aria-label="White wrap with grey polka dots">
    <div class="wrap__lid-line"></div>
    <div class="label label--beige-stripes"><div class="label__plate"><span class="brand">Velvane</span><span class="tagline">Elegant Panties</span><span class="style-tag">hi cut</span></div></div>
    <div class="bow" role="img" aria-label="Black satin bow"></div>
    <div class="size-badge">size</div>
  </article>

  <article class="wrap wrap--charcoal-dots" role="img" aria-label="Black wrap with grey polka dots">
    <div class="wrap__lid-line"></div>
    <div class="label label--grey-dots"><div class="label__plate"><span class="brand">Velvane</span><span class="tagline">Elegant Panties</span><span class="style-tag">hipster</span></div></div>
    <div class="bow" role="img" aria-label="Black satin bow"></div>
    <div class="size-badge">size</div>
  </article>

  <article class="wrap wrap--black-stripes" role="img" aria-label="Black and white vertical pinstripes">
    <div class="wrap__lid-line"></div>
    <div class="label label--magenta-beige"><div class="label__plate"><span class="brand">Velvane</span><span class="tagline">Elegant Panties</span><span class="style-tag">brief</span></div></div>
    <div class="bow" role="img" aria-label="Black satin bow"></div>
    <div class="size-badge">size</div>
  </article>

  <article class="wrap wrap--beige-stripes" role="img" aria-label="Beige and white vertical stripes">
    <div class="wrap__lid-line"></div>
    <div class="label label--magenta-white"><div class="label__plate"><span class="brand">Velvane</span><span class="tagline">Elegant Panties</span><span class="style-tag">hi cut</span></div></div>
    <div class="bow" role="img" aria-label="Black satin bow"></div>
    <div class="size-badge">size</div>
  </article>

  <article class="wrap wrap--white-stripes" role="img" aria-label="White and grey vertical pinstripes">
    <div class="wrap__lid-line"></div>
    <div class="label label--magenta-white"><div class="label__plate"><span class="brand">Velvane</span><span class="tagline">Elegant Panties</span><span class="style-tag">hipster</span></div></div>
    <div class="bow" role="img" aria-label="Black satin bow"></div>
    <div class="size-badge">size</div>
  </article>

</main>
</body>
</html>
```